Fahrzeugaufbereitung inkl. Hol- und Bringedienst
Zielgruppe
Für Privatkunden
Aufgabenstellung
Benötige einen Flyer, um Privatkunden unseren neuen Hol- und Bringedienst für Fahrzeugaufbereitung vorzustellen.
Text und Preise unter www.belvo-fahrdienst.de unter Fahrzeugaufbereitung.
Format Din Lang (105x210mm), zweiseitig

```html
<!DOCTYPE html>
<html lang="de">
<head>
<meta charset="utf-8">
<title>BELVO Fahrzeugaufbereitung – Flyer DIN lang</title>
<link href="https://fonts.googleapis.com/css2?family=Roboto+Condensed:wght@400;700&display=swap" rel="stylesheet">
<style>
:root{
  --blue:#3bb0e3;
  --dark:#1d1d1d;
  --panel:#c5c6c8;
  --panel-light:#d4d5d7;
  --white:#ffffff;
  --stage:#ecebe8;
  --rule:#a9aaac;
}
*{box-sizing:border-box;margin:0;padding:0}
html,body{width:1200px;height:801px;overflow:hidden;background:var(--stage);font-family:"Roboto Condensed",Arial,sans-serif}
.flyer{position:absolute;left:220px;width:760px;height:380px;overflow:hidden;box-shadow:0 4px 14px rgba(0,0,0,.18)}
.flyer--front{top:12px;background:var(--dark)}
.flyer--back{top:408px;background:var(--dark)}
.band-top{position:absolute;left:0;right:0;top:0;height:7px;background:var(--blue);z-index:3}
.band-bottom{position:absolute;left:0;right:0;bottom:0;height:7px;background:var(--rule);z-index:3}

/* front */
.front__side{position:absolute;left:30px;top:7px;bottom:7px;width:180px;background:var(--panel-light);z-index:1}
.brand{position:absolute;left:14px;top:58px;display:flex;align-items:center;gap:8px}
.brand__mark{width:14px;height:14px;background:var(--blue)}
.brand__name{color:var(--blue);font-weight:700;font-size:46px;letter-spacing:1px;line-height:1}
.tabs{position:absolute;left:-22px;top:128px;width:200px}
.tab{position:relative;height:34px;margin-bottom:8px;color:var(--white);font-weight:700;font-size:12.5px;line-height:1.1;display:flex;align-items:center}
.tab__shape{position:absolute;left:0;top:0;z-index:0}
.tab__label{position:relative;z-index:1;padding-left:30px}
.tab--center .tab__label{text-align:center;padding-left:26px}
.front__claim{position:absolute;left:0;right:0;bottom:34px;color:var(--blue);font-weight:700;font-size:19px;line-height:1.25;text-align:center;text-transform:uppercase}
.front__photo{position:absolute;left:210px;top:7px;right:0;bottom:7px;background:radial-gradient(ellipse at 45% 50%,#8a8c8f 0%,#55575a 35%,#2f3033 75%)}
.bubble{position:absolute;left:560px;top:36px;width:184px;padding:10px 12px;background:var(--blue);border:3px solid var(--white);border-radius:12px;color:var(--white);font-weight:700;font-size:19px;line-height:1.15;text-align:center;z-index:2}

/* back */
.back__body{position:absolute;left:52px;top:28px;width:460px;color:var(--white)}
.back__kicker{font-weight:700;font-size:22px;text-transform:uppercase;letter-spacing:.2px}
.back__title{font-weight:700;font-size:38px;line-height:1.1;margin-bottom:10px}
.back__intro{font-size:14px;font-weight:700;line-height:1.2;margin-bottom:18px}
.back__subhead{color:var(--blue);font-weight:700;font-size:18px;margin-bottom:6px}
.services{list-style:none;font-size:15px;line-height:1.18}
.services li{position:relative;padding-left:22px}
.services li::before{content:"";position:absolute;left:0;top:7px;width:5px;height:5px;border-radius:50%;background:var(--blue)}
.back__panel{position:absolute;left:540px;top:7px;bottom:7px;width:186px;background:var(--panel);padding:200px 0 0 12px;color:var(--white)}
.contact__head{color:var(--blue);font-weight:700;font-size:15px;margin-bottom:14px}
.contact__address{font-style:normal;font-weight:700;font-size:14px;line-height:1.25;margin-bottom:16px}
.contact__lines{font-size:13px;font-weight:700;line-height:1.4;white-space:nowrap}
.contact__lines b{display:inline-block;width:14px}
</style>
</head>
<body>

<section class="flyer flyer--front" aria-label="Vorderseite">
  <div class="band-top"></div>
  <div class="front__photo" role="img" aria-label="Foto von oben: weißes Cabrio wird von mehreren Mitarbeitern in weißer Kleidung und blauen Mützen gereinigt und poliert"></div>
  <div class="front__side">
    <div class="brand">
      <span class="brand__mark"></span>
      <span class="brand__name">BELVO</span>
    </div>
    <div class="tabs">
      <div class="tab tab--center">
        <svg class="tab__shape" width="186" height="34" viewBox="0 0 186 34"><polygon points="0,0 186,0 164,34 0,34" fill="#3bb0e3"/></svg>
        <span class="tab__label">Erstklassische<br>Fahrzeugaufbereitung</span>
      </div>
      <div class="tab">
        <svg class="tab__shape" width="158" height="34" viewBox="0 0 158 34"><polygon points="0,0 158,0 136,34 0,34" fill="#3bb0e3"/></svg>
        <span class="tab__label">Professioneller Service</span>
      </div>
      <div class="tab">
        <svg class="tab__shape" width="130" height="34" viewBox="0 0 130 34"><polygon points="0,0 130,0 108,34 0,34" fill="#3bb0e3"/></svg>
        <span class="tab__label" style="padding-left:48px">59,90€</span>
      </div>
    </div>
    <p class="front__claim">Dienstleistungen<br>rund ums Auto</p>
  </div>
  <p class="bubble">Bei uns ist ihr Auto in guten Händen!</p>
  <div class="band-bottom"></div>
</section>

<section class="flyer flyer--back" aria-label="Rückseite">
  <div class="band-top"></div>
  <div class="back__body">
    <p class="back__kicker">Klassische Fahrzeugaufbereitung</p>
    <h1 class="back__title">inkl. Hol und Bringedienst</h1>
    <p class="back__intro">Wir bieten Ihnen eine klassische Fahrzeugaufbereitung inkl. Hol- und Bringedienst in Berlin und München für nur 59,90 € an. Sparen Sie Ihre wertvolle Zeit und lassen Sie Ihr Fahrzeug von uns an Ihrem Wunschort abholen und innerhalb der nächsten 90 Minuten aufbereiten.</p>
    <h2 class="back__subhead">Unser Leitungsangebot enthält</h2>
    <ul class="services">
      <li>Hol- und Bringeservic</li>
      <li>Aussenwäsche inkl. Felgenreinigung</li>
      <li>Innenreinigung inkl. Cockpit und Saugen</li>
      <li>Fensterreinigung innen &amp; aussen</li>
      <li>Öl-, Wasser- und Wischwasserkontrolle</li>
      <li>Reifendruck und Profilkontrolle</li>
    </ul>
  </div>
  <aside class="back__panel">
    <p class="contact__head">Kontaktieren Sie uns!</p>
    <address class="contact__address">B.E.L.V.O. GmbH<br>Lindenhofweg 42<br>10437 Berlin</address>
    <p class="contact__lines"><b>T</b>030 41 72 55 6 - 0<br><b>F</b>030 41 72 55 6 - 11<br><b>E</b>info@belvo-fahrdienst.de</p>
  </aside>
  <div class="band-bottom"></div>
</section>

</body>
</html>
```